Business Card Design Project

We are a construction company in Orange County, CA. We need a two sided business card. We would like the back to be our logo with web URL. Front should included Name, title, address, phone, fax and email address.

our address is
627 West Dorrance Blvd, Suite 308
Anaheim, CA 92718

Our logo files are attached.

Construction

```html
<!DOCTYPE html>
<html lang="en">
<head>
<meta charset="utf-8">
<title>Halvern Business Card</title>
<link rel="stylesheet" href="https://fonts.googleapis.com/css2?family=Montserrat:wght@300;400;700&display=swap">
<style>
  :root {
    --brand-blue: #1a4a7c;
    --card-white: #ffffff;
    --page-bg: #e9e7e4;
    --text-white: #ffffff;
  }
  * { margin: 0; padding: 0; box-sizing: border-box; }
  html, body { width: 1200px; height: 431px; overflow: hidden; }
  body {
    background: var(--page-bg);
    font-family: "Montserrat", Arial, sans-serif;
    position: relative;
  }
  .card {
    position: absolute;
    top: 61px;
    width: 538px;
    height: 308px;
    border-radius: 14px;
    background: var(--card-white);
    overflow: hidden;
    box-shadow: 0 2px 6px rgba(0,0,0,0.18);
  }
  .card-front { left: 48px; }
  .card-back { left: 613px; }

  .front-art { position: absolute; inset: 0; display: block; }
  .front-art text { fill: var(--text-white); font-family: "Montserrat", Arial, sans-serif; }
  .holder-name { font-weight: 700; font-size: 15px; letter-spacing: 0.3px; }
  .holder-address { font-weight: 300; font-size: 13px; }
  .front-brand { font-weight: 700; font-size: 52px; }
  .contact-text { font-weight: 300; font-size: 13px; }

  .back-brand {
    position: absolute;
    left: 0; right: 0;
    top: 112px;
    text-align: center;
    color: var(--brand-blue);
    font-weight: 700;
    font-size: 58px;
    letter-spacing: -1px;
  }
  .back-url {
    position: absolute;
    left: 0; right: 0;
    top: 210px;
    text-align: center;
    color: var(--brand-blue);
    font-weight: 400;
    font-size: 13px;
    letter-spacing: 2.5px;
  }
</style>
</head>
<body>

<section class="card card-front">
  <svg class="front-art" width="538" height="308" viewBox="0 0 538 308">
    <polygon class="band-upper" fill="var(--brand-blue)" points="0,0 273,0 287,15 70,223 0,150"/>
    <polygon class="band-lower" fill="var(--brand-blue)" points="288,25 538,286 538,308 143,308 71,233"/>

    <g transform="rotate(-44)">
      <text class="holder-name" x="-22" y="117">YOUR NAME</text>
      <text class="holder-address" x="-23" y="158">627 West Dorrance Blvd</text>
      <text class="holder-address" x="-23" y="176">Suite 308</text>
      <text class="holder-address" x="-23" y="194">Anaheim, CA 92718</text>

      <text class="front-brand" x="-87" y="262" textLength="268" lengthAdjust="spacingAndGlyphs">HALVERN</text>

      <g class="contact-phone" transform="translate(-14,315)">
        <circle cx="5" cy="5" r="4.5" fill="none" stroke="#fff" stroke-width="1"/>
        <rect x="3.5" y="2.5" width="3" height="5" rx="0.8" fill="#fff"/>
      </g>
      <text class="contact-text" x="2" y="324">0923456781</text>

      <g class="contact-fax" transform="translate(-14,333)">
        <rect x="1" y="3" width="8" height="5" rx="1" fill="#fff"/>
        <rect x="3" y="1" width="4" height="2" fill="#fff"/>
      </g>
      <text class="contact-text" x="2" y="342">0923456781</text>

      <g class="contact-email" transform="translate(-14,351)">
        <rect x="0.5" y="2" width="9" height="6" fill="#fff"/>
        <polyline points="0.5,2 5,5.5 9.5,2" fill="none" stroke="var(--brand-blue)" stroke-width="1"/>
      </g>
      <text class="contact-text" x="2" y="360">info@halvernbuild.com</text>

      <g class="contact-web" transform="translate(-14,368)">
        <circle cx="5" cy="5" r="4.5" fill="#fff"/>
        <line x1="0.5" y1="5" x2="9.5" y2="5" stroke="var(--brand-blue)" stroke-width="0.8"/>
        <ellipse cx="5" cy="5" rx="2" ry="4.5" fill="none" stroke="var(--brand-blue)" stroke-width="0.8"/>
      </g>
      <text class="contact-text" x="2" y="377">www.halvernbuild.com</text>
    </g>
  </svg>
</section>

<section class="card card-back">
  <div class="back-brand">HALVERN</div>
  <div class="back-url">www.halvernbuild.com</div>
</section>

</body>
</html>
```